Corporate Business Card

Very professional, Modern, Not to busy, include phone address email, website
(253) 617-4930, 18761 52nd Avenue S, Alder, OR 98047, martin@plumlinegroup.com, varkoworks.com

Target Market(s)

Manufacturing

Industry/Entity Type

Aero, machining, manufacturing, Off road racing

Contact Information for Business Card

Phone, address email, website

```html
<!DOCTYPE html>
<html lang="en">
<head>
<meta charset="utf-8">
<title>Varko Works Business Card</title>
<link rel="stylesheet" href="https://fonts.googleapis.com/css2?family=Montserrat:wght@400;500;700&display=swap">
<style>
  :root {
    --backdrop: #d3cbbb;
    --card-white: #ffffff;
    --card-black: #161616;
    --navy: #13306b;
    --ink: #1c1c1c;
    --emboss: #2b2b2b;
  }
  * { margin: 0; padding: 0; box-sizing: border-box; }
  html, body {
    width: 1116px;
    height: 1200px;
    overflow: hidden;
    background: var(--backdrop);
    font-family: "Montserrat", Arial, sans-serif;
  }
  .card {
    position: absolute;
    left: 224px;
    width: 669px;
    height: 385px;
    border-radius: 26px;
  }
  .card-front { top: 177px; background: var(--card-white); }
  .card-back { top: 639px; background: var(--card-black); }

  .brand-name {
    position: absolute;
    left: 0;
    right: 0;
    text-align: center;
    font-weight: 700;
    letter-spacing: 2px;
    white-space: nowrap;
  }
  .card-front .brand-name {
    top: 38px;
    font-size: 58px;
    color: var(--navy);
  }
  .card-back .brand-name {
    top: 130px;
    font-size: 66px;
    color: var(--emboss);
  }

  .person {
    position: absolute;
    top: 199px;
    left: 0;
    right: 0;
    text-align: center;
  }
  .person-name {
    font-size: 25px;
    font-weight: 700;
    color: var(--navy);
    letter-spacing: 0.3px;
  }
  .person-title {
    margin-top: 2px;
    font-size: 16px;
    font-weight: 500;
    color: var(--ink);
  }

  .address {
    position: absolute;
    top: 300px;
    right: 346px;
    text-align: right;
    font-size: 16.5px;
    font-style: normal;
    line-height: 26px;
    color: var(--ink);
    white-space: nowrap;
  }
  .divider {
    position: absolute;
    left: 334px;
    top: 278px;
    width: 2px;
    height: 70px;
    background: var(--navy);
  }
  .contact-list {
    position: absolute;
    left: 350px;
    top: 286px;
    list-style: none;
    font-size: 16.5px;
    line-height: 26px;
    color: var(--ink);
    white-space: nowrap;
  }
  .contact-list li { display: flex; align-items: center; gap: 5px; }
  .contact-list svg { width: 14px; height: 14px; fill: var(--navy); flex: none; }
</style>
</head>
<body>
  <section class="card card-front">
    <div class="brand-name">VARKO WORKS</div>

    <div class="person">
      <div class="person-name">DANIEL REYES</div>
      <div class="person-title">Owner/CEO</div>
    </div>

    <address class="address">
      1140, 18761 52nd Avenue<br>S, Alder, OR 98047
    </address>

    <div class="divider"></div>

    <ul class="contact-list">
      <li>
        <svg viewBox="0 0 24 24" aria-hidden="true"><path d="M6.6 10.8a15.1 15.1 0 0 0 6.6 6.6l2.2-2.2c.3-.3.7-.4 1-.2 1.1.4 2.3.6 3.6.6.6 0 1 .4 1 1V20c0 .6-.4 1-1 1A17 17 0 0 1 3 4c0-.6.4-1 1-1h3.5c.6 0 1 .4 1 1 0 1.3.2 2.5.6 3.6.1.3 0 .7-.2 1z"/></svg>
        (555) 617-4930
      </li>
      <li>
        <svg viewBox="0 0 24 24" aria-hidden="true"><path d="M2 5h20v2l-10 6L2 7zm0 4.3 10 6 10-6V19H2z"/></svg>
        martin@plumlinegroup.com
      </li>
      <li>
        <svg viewBox="0 0 24 24" aria-hidden="true"><path d="M12 2a10 10 0 1 0 0 20 10 10 0 0 0 0-20zm6.9 6h-2.9a15.6 15.6 0 0 0-1.4-3.6A8 8 0 0 1 18.9 8zM12 4c.8 1.2 1.5 2.5 1.9 4h-3.8c.4-1.5 1.1-2.8 1.9-4zM4.3 14a8 8 0 0 1 0-4h3.4a16 16 0 0 0 0 4zm.8 2h2.9c.3 1.3.8 2.5 1.4 3.6A8 8 0 0 1 5.1 16zM8 8H5.1a8 8 0 0 1 4.3-3.6C8.8 5.5 8.3 6.7 8 8zm4 12c-.8-1.2-1.5-2.5-1.9-4h3.8c-.4 1.5-1.1 2.8-1.9 4zm2.3-6H9.7a14.6 14.6 0 0 1 0-4h4.6a14.6 14.6 0 0 1 0 4zm.3 5.6c.6-1.1 1.1-2.3 1.4-3.6h2.9a8 8 0 0 1-4.3 3.6zM16.3 14a16 16 0 0 0 0-4h3.4a8 8 0 0 1 0 4z"/></svg>
        www.varkoworks.com
      </li>
    </ul>
  </section>

  <section class="card card-back">
    <div class="brand-name">VARKO WORKS</div>
  </section>
</body>
</html>
```